Simple and Clean business card design

We would like the design to be simple clean and to incorporate our colors.

We are open to your design and talent, we have the dots in our logo as we think of it as data points and we connect data points for people.

We are open to see the great creative and clean design you bring to the table

Contact Information for Business Card

please include: name, position, email, phone and website

Font styles to use
Sans Serif

Requirements
Must have
• my colors incorporated, simplicity
Nice to have
• lots of white space, simplicity
Should not have
• complexicity/ complex art

```html
<!DOCTYPE html>
<html lang="en">
<head>
<meta charset="utf-8">
<title>Veltrix Business Card</title>
<link rel="stylesheet" href="https://fonts.googleapis.com/css2?family=Montserrat:wght@500&family=Jost:wght@400;700&display=swap">
<style>
  :root {
    --backdrop: #9b9b9b;
    --card: #ffffff;
    --ink: #161616;
    --text: #3d3d3d;
    --blue: #5b84c4;
    --green: #32a852;
  }
  * { margin: 0; padding: 0; box-sizing: border-box; }
  html, body {
    width: 1021px;
    height: 1200px;
    overflow: hidden;
    background: var(--backdrop);
  }
  .card {
    position: absolute;
    left: 133px;
    width: 753px;
    height: 429px;
    background: var(--card);
  }
  .card--front { top: 119px; }
  .card--back { top: 651px; }

  .wordmark {
    position: absolute;
    font-family: "Montserrat", sans-serif;
    font-weight: 500;
    color: var(--ink);
    line-height: 1;
    white-space: nowrap;
    display: flex;
    align-items: center;
  }
  .wordmark__dot {
    display: inline-block;
    border-radius: 50%;
    background: var(--blue);
  }
  .card--front .wordmark {
    left: 0; right: 0;
    top: 150px;
    justify-content: center;
    font-size: 138px;
    letter-spacing: 2px;
  }
  .card--front .wordmark__dot {
    width: 30px; height: 30px;
    margin-right: 22px;
    margin-top: 40px;
  }
  .card--back .wordmark {
    right: 36px;
    top: 68px;
    font-size: 76px;
    letter-spacing: 1px;
  }
  .card--back .wordmark__dot {
    width: 17px; height: 17px;
    margin-right: 12px;
    margin-top: 22px;
  }

  .details {
    position: absolute;
    left: 0;
    top: 257px;
    font-family: "Jost", sans-serif;
  }
  .details__bar {
    position: absolute;
    left: 0;
    top: 4px;
    width: 16px;
    height: 40px;
    background: var(--green);
  }
  .details__company {
    margin-left: 36px;
    font-weight: 700;
    font-size: 27px;
    line-height: 30px;
    color: var(--blue);
    letter-spacing: 0.3px;
  }
  .details__role {
    margin-left: 36px;
    font-size: 18px;
    line-height: 24px;
    color: var(--text);
  }
  .contact {
    list-style: none;
    margin: 14px 0 0 36px;
  }
  .contact__item {
    display: flex;
    align-items: center;
    font-size: 18px;
    line-height: 25px;
    color: var(--text);
  }
  .contact__icon {
    width: 13px;
    height: 13px;
    margin-right: 8px;
    fill: var(--blue);
    flex: none;
  }
</style>
</head>
<body>
  <section class="card card--front">
    <div class="wordmark"><span class="wordmark__dot"></span>Veltrix</div>
  </section>

  <section class="card card--back">
    <div class="wordmark"><span class="wordmark__dot"></span>Veltrix</div>

    <div class="details">
      <span class="details__bar"></span>
      <p class="details__company">VELTRIX.IO</p>
      <p class="details__role">Founder/ CEO</p>
      <ul class="contact">
        <li class="contact__item">
          <svg class="contact__icon" viewBox="0 0 16 16" aria-hidden="true"><path d="M3.6 1.2l2.2 2.6-1.3 1.6c.9 2.2 2.6 3.9 4.8 4.8l1.6-1.3 2.6 2.2-1.4 2.6C6.9 13.3 2.7 9.1 1 3z"/></svg>
          555-014-2290
        </li>
        <li class="contact__item">
          <svg class="contact__icon" viewBox="0 0 16 16" aria-hidden="true"><path d="M1 3h14v10H1z M2.2 4.2v.3L8 9l5.8-4.5v-.3z" fill-rule="evenodd"/></svg>
          dana.ellis@veltrix.io
        </li>
        <li class="contact__item">
          <svg class="contact__icon" viewBox="0 0 16 16" aria-hidden="true"><circle cx="8" cy="8" r="7"/><path d="M4 4.5c1.5.5 2 1.8 1.4 3L7 9.5 6 13M10 2.5c-.5 1.5.5 2.5 2 2.5M11 9l2 1.5-1.5 2" stroke="#fff" stroke-width="1.1" fill="none"/></svg>
          www.Veltrix.io
        </li>
      </ul>
    </div>
  </section>
</body>
</html>
```